Velvet Dice Night Age Verification Landing Page

To create a visually appealing design for the landing page of the adult game "Velvet Dice Night" that confirms the visitor's age.
The design should have a simple and visually appealing look that focuses on two buttons labeled "Yes" and "No". The purpose of the page is to confirm that the visitor is 18 years of age or older before accessing the game's content. Responsive design that works well on desktop and mobile devices. The final output should be delivered in PSD, AI, or Sketch format, along with any necessary images or assets.
I have also attached examples.

```html
<!DOCTYPE html>
<html lang="en">
<head>
<meta charset="UTF-8">
<title>Velvet Dice Night — Age Verification</title>
<link rel="stylesheet" href="https://fonts.googleapis.com/css2?family=Montserrat:wght@400;500;600&display=swap">
<style>
  :root {
    --bg-dark: #1c1c20;
    --bg-mid: #3a3a42;
    --panel: rgba(20, 20, 22, 0.92);
    --purple: #7d5aa6;
    --purple-light: #a57ccf;
    --text: #ffffff;
    --text-soft: #d8d8dc;
    --line: rgba(255, 255, 255, 0.45);
  }
  * { margin: 0; padding: 0; box-sizing: border-box; }
  html, body { width: 1067px; height: 1200px; overflow: hidden; }
  body { font-family: "Montserrat", Arial, sans-serif; background: var(--bg-dark); color: var(--text); }
  .stage { position: relative; width: 1067px; height: 1200px; overflow: hidden; }
  .hero-photo {
    position: absolute; inset: 0;
    background:
      radial-gradient(ellipse 260px 420px at 430px 560px, rgba(150, 90, 70, 0.45), transparent 70%),
      radial-gradient(ellipse 220px 260px at 830px 250px, rgba(160, 80, 60, 0.35), transparent 70%),
      radial-gradient(ellipse 500px 700px at 50% 50%, #4a4a52, var(--bg-mid) 60%, var(--bg-dark));
  }
  .music-toggle {
    position: absolute; left: 974px; top: 13px; width: 50px; height: 50px;
    border: 2px solid var(--line); border-radius: 8px;
    display: flex; align-items: center; justify-content: center;
  }
  .frame-line { position: absolute; background: var(--line); }
  .frame-dot { position: absolute; width: 6px; height: 6px; border-radius: 50%; background: #fff; }
  .age-panel {
    position: absolute; left: 78px; top: 356px; width: 911px; height: 489px;
    background: var(--panel);
    display: flex; flex-direction: column; align-items: center;
  }
  .brand {
    margin-top: 72px; display: flex; align-items: center; gap: 18px;
    font-size: 40px; font-weight: 600; color: var(--purple-light); letter-spacing: 0.5px;
  }
  .brand-dot { width: 26px; height: 26px; border-radius: 50%; background: var(--purple-light); }
  .age-question { margin-top: 82px; font-size: 24px; font-weight: 500; letter-spacing: 0.5px; }
  .answer-row { margin-top: 24px; display: flex; gap: 9px; }
  .answer-btn {
    width: 143px; height: 58px; background: var(--purple); color: var(--text);
    border: none; font-family: inherit; font-size: 19px; font-weight: 500; letter-spacing: 1px;
  }
  .remember {
    margin-top: 42px; display: flex; align-items: center; gap: 10px;
    font-size: 17px; color: var(--text-soft);
  }
  .remember-box { width: 17px; height: 17px; background: #e8e8ea; border-radius: 3px; }
</style>
</head>
<body>
<div class="stage">
  <div class="hero-photo" role="img" aria-label="Background photograph of a smiling woman in leather trousers against a grey studio wall"></div>

  <div class="music-toggle">
    <svg width="26" height="26" viewBox="0 0 24 24" fill="none" stroke="#fff" stroke-width="2">
      <path d="M9 18V5l11-2v13"/>
      <circle cx="6" cy="18" r="3" fill="#fff"/>
      <circle cx="17" cy="16" r="3" fill="#fff"/>
    </svg>
  </div>

  <div class="frame-line" style="left:44px; top:373px; width:978px; height:1px;"></div>
  <div class="frame-line" style="left:44px; top:826px; width:978px; height:1px;"></div>
  <div class="frame-line" style="left:73px; top:350px; width:1px; height:550px;"></div>
  <div class="frame-line" style="left:989px; top:290px; width:1px; height:565px;"></div>
  <div class="frame-dot" style="left:71px; top:370px;"></div>
  <div class="frame-dot" style="left:1016px; top:370px;"></div>
  <div class="frame-dot" style="left:71px; top:823px;"></div>
  <div class="frame-dot" style="left:1016px; top:823px;"></div>
  <div class="frame-dot" style="left:986px; top:290px;"></div>
  <div class="frame-dot" style="left:986px; top:851px;"></div>

  <section class="age-panel">
    <div class="brand"><span class="brand-dot"></span>Velvet Dice Night</div>
    <p class="age-question">Are you over 18 Years of age?</p>
    <div class="answer-row">
      <button class="answer-btn">YES</button>
      <button class="answer-btn">NO</button>
    </div>
    <label class="remember"><span class="remember-box"></span>Remember Me?</label>
  </section>
</div>
</body>
</html>
```